Agriculture Security Company needs a business card design

We need a business card design for a new company based in Seattle calls Ferncrest Guardline LLC. We provide high-end physical security solutions that is geared and focused towards to the marijuana grow operations, wholesalers and distributors. We DO NOT get involved in the retail operations (store fronts). We would like to see designs that incorporate professionalism, reliability, trustworthy and forward thinking as traits of our organization.

Industry/Entity Type

Security

```html
<!DOCTYPE html>
<html lang="en">
<head>
<meta charset="utf-8">
<title>Ferncrest Guardline LLC – Business Card</title>
<link rel="stylesheet" href="https://fonts.googleapis.com/css2?family=Cinzel:wght@700&family=Open+Sans:wght@400;600&display=swap">
<style>
  :root {
    --page: #eeece8;
    --card: #ffffff;
    --card-edge: #e2e2e2;
    --green-dark: #0f6e36;
    --green: #1a8a45;
    --green-light: #7cb342;
    --blue: #5b8fc9;
    --text-light: #ffffff;
    --text-soft: #d9efe0;
  }
  * { margin: 0; padding: 0; box-sizing: border-box; }
  html, body { width: 1200px; height: 1023px; overflow: hidden; }
  body {
    background: var(--page);
    font-family: "Open Sans", Arial, sans-serif;
    position: relative;
  }
  .card {
    position: absolute;
    width: 560px;
    height: 320px;
    background: var(--card);
    border: 1px solid var(--card-edge);
    box-shadow: 0 6px 18px rgba(0,0,0,0.12);
    overflow: hidden;
  }
  .card--front { left: 90px; top: 130px; }
  .card--back { left: 550px; top: 560px; }

  .brand {
    position: absolute;
    display: flex;
    flex-direction: column;
    align-items: flex-start;
  }
  .brand__name {
    font-family: "Cinzel", Georgia, serif;
    font-weight: 700;
    color: var(--green-dark);
    line-height: 1.05;
  }
  .brand__tag {
    font-family: "Open Sans", Arial, sans-serif;
    font-size: 10px;
    letter-spacing: 1.5px;
    color: #5a6b5e;
    margin-top: 6px;
  }
  .card--front .brand { left: 40px; top: 34px; }
  .card--front .brand__name { font-size: 30px; }

  .band {
    position: absolute;
    left: 0; right: 0;
    top: 150px;
    height: 124px;
    background: linear-gradient(180deg, var(--green) 0%, var(--green-dark) 100%);
    border-bottom: 4px solid var(--blue);
    display: flex;
    align-items: center;
    color: var(--text-light);
  }
  .person { padding-left: 40px; width: 250px; }
  .person__name { font-size: 21px; font-weight: 600; }
  .person__role { font-size: 12px; color: var(--text-soft); margin-bottom: 10px; }
  .person__address { font-size: 11px; line-height: 1.55; color: var(--text-soft); }
  .band__divider {
    width: 1px; height: 84px;
    background: rgba(255,255,255,0.45);
    margin-right: 22px;
  }
  .contacts { list-style: none; font-size: 11px; line-height: 2; }
  .contacts li { display: flex; align-items: center; gap: 8px; }
  .contacts svg { width: 12px; height: 12px; fill: var(--text-light); flex: none; }

  .card--back .brand {
    left: 0; right: 0; top: 100px;
    align-items: center;
  }
  .card--back .brand__name { font-size: 34px; }
  .card--back .website {
    position: absolute;
    left: 30px; bottom: 24px;
    font-size: 13px;
    letter-spacing: 2px;
    color: var(--green-light);
  }
</style>
</head>
<body>
  <section class="card card--front">
    <div class="brand">
      <span class="brand__name">Ferncrest Guardline</span>
      <span class="brand__tag">LLC · PROTECTING THE FUTURE</span>
    </div>
    <div class="band">
      <div class="person">
        <p class="person__name">Daniel Hale</p>
        <p class="person__role">president</p>
        <p class="person__address">740 Cedar Ridge Ave<br>Suite 118 Seattle</p>
      </div>
      <div class="band__divider"></div>
      <ul class="contacts">
        <li><svg viewBox="0 0 24 24"><path d="M6.6 10.8a15 15 0 0 0 6.6 6.6l2.2-2.2c.3-.3.7-.4 1-.2 1.1.4 2.3.6 3.6.6.6 0 1 .4 1 1V20c0 .6-.4 1-1 1A17 17 0 0 1 3 4c0-.6.4-1 1-1h3.5c.6 0 1 .4 1 1 0 1.3.2 2.5.6 3.6.1.3 0 .7-.2 1z"/></svg>555-014-2291</li>
        <li><svg viewBox="0 0 24 24"><path d="M2 5h20v14H2z M2 5l10 8 10-8" fill="none" stroke="#fff" stroke-width="2"/></svg>info@ferncrestguardline.com</li>
        <li><svg viewBox="0 0 24 24"><circle cx="12" cy="12" r="10"/></svg>www.ferncrestguardline.com</li>
      </ul>
    </div>
  </section>

  <section class="card card--back">
    <div class="brand">
      <span class="brand__name">Ferncrest Guardline</span>
      <span class="brand__tag">LLC · PROTECTING THE FUTURE</span>
    </div>
    <p class="website">www.ferncrestguardline.com</p>
  </section>
</body>
</html>
```